Merrowin Vodka logo and label design

We would like a logo and bottle label design for a new line of Ultra-Premium Vodka. The Company is called Merrowin Spirits and is based in Brisbane, Australia. We would like a 'Gatsby/Prohibition era vibe to the design. We want to keep it minimalistic and sleek. We strongly prefer a minimalist design and colour palette. Black,Gold,Grey,White,Silver,Red and Blue

The bottle will be similar in shape to Castellane/Blue Heron. There will also need to be space on the label for required information, as well as short bio of the company, which will be provided to the winning design.
Updates

We would like to add the polish code of arms for Opoczno. Have attached link for reference. https://www.crestarchive-demo.net/crestwiki/index.php?title=Opoczno

Target Market(s)

Luxury brand customers

Logo Text

Merrowin Ultra-Premium Vodka

Logo styles of interest
Wordmark Logo
Lettermark Logo
Requirements
Must have
• This is the first release from our new Vodka label. We want a logo and bottle label that reflects a premium product. We very much like Prohibition/Gatsby era themed bottles and labels. The label and bottle should be elegant and clean.
Should not have
• Anything too busy or confusing.

```html
<!DOCTYPE html>
<html lang="en">
<head>
<meta charset="utf-8">
<title>Merrowin Ultra-Premium Vodka – Bottle Label</title>
<link rel="stylesheet" href="https://fonts.googleapis.com/css2?family=Cinzel:wght@400&family=Josefin+Sans:wght@600&family=Libre+Caslon+Text&family=Arimo:wght@400&display=swap">
<style>
  :root {
    --backdrop: #2a2b2b;
    --label-black: #0b0b0b;
    --label-edge: #1c1c1c;
    --gold: #d9b45a;
    --gold-light: #f2dc93;
    --gold-deep: #a9782c;
    --print-grey: #d7d9d9;
  }
  html, body {
    margin: 0;
    padding: 0;
    width: 1200px;
    height: 2814px;
    overflow: hidden;
    background: var(--backdrop);
  }
  .canvas {
    position: relative;
    width: 1200px;
    height: 2814px;
  }
  .label {
    position: absolute;
    left: 95px;
    top: 230px;
    width: 1010px;
    height: 1866px;
  }
  .wordmark {
    font-family: "Cinzel", serif;
    font-weight: 400;
    font-size: 68px;
    fill: var(--gold);
  }
  .tagline {
    font-family: "Josefin Sans", sans-serif;
    font-weight: 600;
    font-size: 13.5px;
    letter-spacing: 4.6px;
    fill: var(--gold);
  }
  .info-field {
    font-family: "Libre Caslon Text", serif;
    font-size: 11.5px;
    fill: var(--gold);
  }
  .glass-print {
    position: absolute;
    left: 216px;
    top: 2150px;
    font-family: "Arimo", sans-serif;
    color: var(--print-grey);
    line-height: 1.2;
  }
  .glass-print p { margin: 0; }
  .glass-print .descriptor { font-size: 36px; }
  .glass-print .measure { font-size: 54px; letter-spacing: -1px; }
  .glass-print .origin { font-size: 36px; margin-top: 110px; }
</style>
</head>
<body>
<main class="canvas">
  <svg class="label" viewBox="0 0 460 850" role="img" aria-label="Merrowin Ultra-Premium Vodka label">
    <defs>
      <linearGradient id="label-fill" x1="0" x2="1" y1="0" y2="0">
        <stop offset="0" stop-color="var(--label-edge)"/>
        <stop offset="0.5" stop-color="var(--label-black)"/>
        <stop offset="1" stop-color="#000"/>
      </linearGradient>
      <linearGradient id="gold-rule" x1="0" x2="1" y1="0" y2="0">
        <stop offset="0" stop-color="var(--gold-deep)"/>
        <stop offset="0.5" stop-color="var(--gold-light)"/>
        <stop offset="1" stop-color="var(--gold-deep)"/>
      </linearGradient>
    </defs>

    <path class="label-shape" fill="url(#label-fill)" stroke="url(#gold-rule)" stroke-width="5"
      d="M2.5,97 H93 C118,97 124,62 145,37 C168,10 198,2.5 230,2.5 C262,2.5 292,10 315,37 C336,62 342,97 367,97 H457.5
         V743 H367 C342,743 336,778 315,803 C292,830 262,847.5 230,847.5 C198,847.5 168,830 145,803 C124,778 118,743 93,743 H2.5 Z"/>

    <g class="rules-top" fill="url(#gold-rule)">
      <ellipse cx="230" cy="62" rx="66" ry="2.4"/>
      <ellipse cx="230" cy="86" rx="66" ry="2.4"/>
      <ellipse cx="230" cy="110" rx="66" ry="2.4"/>
    </g>

    <text class="wordmark" x="230" y="482" text-anchor="middle">MERROWIN</text>
    <text class="tagline" x="232" y="504" text-anchor="middle">ULTRA-PREMIUM VODKA</text>

    <g class="info-table" stroke="var(--gold)" fill="none">
      <rect x="100" y="556" width="257" height="98" stroke-width="2"/>
      <line x1="228.5" y1="562" x2="228.5" y2="648" stroke-width="2"/>
      <line x1="108" y1="604" x2="342" y2="604" stroke-width="2"/>
    </g>
    <text class="info-field" x="118" y="589">BATCH</text>
    <text class="info-field" x="243" y="589">ALC/VOL</text>
    <text class="info-field" x="118" y="629">YEAR</text>
    <text class="info-field" x="243" y="629">ML</text>

    <g class="rules-bottom" fill="url(#gold-rule)">
      <ellipse cx="230" cy="710" rx="132" ry="2.4"/>
      <ellipse cx="230" cy="743" rx="100" ry="2.4"/>
      <ellipse cx="230" cy="778" rx="77" ry="2.4"/>
    </g>
  </svg>

  <section class="glass-print">
    <p class="descriptor">Premium Czech Vodka</p>
    <p class="descriptor">Infused with Artemisia Absinthium</p>
    <p class="measure">40% alc</p>
    <p class="measure">750ml ℮</p>
    <p class="origin">Imported from the Czech Republic</p>
  </section>
</main>
</body>
</html>
```